Detail Shop Business card design

i need a business card design for my new detailing company called 'Brisk's Polish Works'. i want an all black and white design . simple, direct and to the point. i want the designer to choose a fitting font to match the logothe front should have logo, address, phone and email and the back side should have a slogan and text indicating that we offer services on anything including cars, trucks, motorcycles and RVs. slogan will read "we take pride in your ride"
maybe also very small on the back side the IG icon with Brisks_Polish_Works

phone 208.417.6352
address 3847 E Larkin Ave
Spokane WA 99214
email: BrisksPolish@mailvexo.com

Target Market(s)

all ages , auto enthusiasts

Industry/Entity Type

Automotive

Contact Information for Business Card

the front should have logo, address, phone and email and the back side should have a slogan and text indicating that we offer services on anything including cars, trucks, motorcycles and RVs. slogan will read "we take pride in your ride"

phone 208.417.6352
address 3847 E Larkin Ave
Spokane WA 99214

Colors
000000
ffffff

Requirements
Must have
• bold font and very simple design with good spacing
Nice to have
• anything creative from the designer indicating we service any types of vehicles
Should not have
• any colors ,

```html
<!DOCTYPE html>
<html lang="en">
<head>
<meta charset="utf-8">
<title>Brisk's Polish Works — Business Card</title>
<link href="https://fonts.googleapis.com/css2?family=Lato:wght@400;700&display=swap" rel="stylesheet">
<style>
  :root {
    --backdrop: #4a4a4a;
    --card-light: #f3f3f3;
    --card-dark: #0b0b0b;
    --ink: #111111;
    --paper: #ffffff;
    --rule: #b9b9b9;
  }
  * { margin: 0; padding: 0; box-sizing: border-box; }
  html, body {
    width: 1200px;
    height: 900px;
    overflow: hidden;
    background: var(--backdrop);
    font-family: 'Lato', Arial, sans-serif;
  }
  .stage { position: relative; width: 1200px; height: 900px; }

  .card {
    position: absolute;
    top: 200px;
    width: 310px;
    height: 502px;
  }
  .card--front {
    left: 252px;
    background: var(--card-light);
    color: var(--ink);
    border-radius: 56px 0 56px 0;
  }
  .card--back {
    left: 627px;
    background: var(--card-dark);
    color: var(--paper);
    border-radius: 0 56px 0 56px;
  }

  .brand {
    position: absolute;
    left: 0;
    width: 100%;
    display: flex;
    flex-direction: column;
    align-items: center;
    gap: 14px;
  }
  .card--front .brand { top: 92px; }
  .card--back .brand { top: 66px; }
  .brand__dot {
    width: 70px;
    height: 70px;
    border-radius: 50%;
    background: currentColor;
  }
  .brand__name {
    font-weight: 700;
    font-size: 25px;
    letter-spacing: 0.5px;
    text-align: center;
    line-height: 1.15;
  }

  .contact {
    position: absolute;
    left: 33px;
    top: 332px;
    font-size: 14px;
    line-height: 19px;
  }
  .contact__line { display: flex; align-items: center; gap: 5px; }
  .contact__line svg { width: 11px; height: 11px; fill: var(--ink); }
  .contact__address { margin-top: 15px; padding-left: 2px; }
  .contact__rule {
    position: absolute;
    left: 33px;
    top: 433px;
    width: 220px;
    height: 1px;
    background: var(--rule);
  }
  .social {
    position: absolute;
    left: 33px;
    top: 451px;
    display: flex;
    align-items: center;
    gap: 5px;
    font-size: 14px;
  }
  .social__mark {
    width: 19px;
    height: 19px;
    border-radius: 50%;
    background: var(--ink);
  }

  .slogan {
    position: absolute;
    left: 0;
    top: 251px;
    width: 100%;
    text-align: center;
    font-size: 17.5px;
    letter-spacing: 0.3px;
  }
  .services {
    position: absolute;
    left: 38px;
    top: 330px;
    font-size: 18px;
    line-height: 30px;
  }
</style>
</head>
<body>
<main class="stage">

  <section class="card card--front" aria-label="Card front">
    <div class="brand">
      <span class="brand__dot" aria-hidden="true"></span>
      <span class="brand__name">Brisk's Polish Works</span>
    </div>

    <div class="contact">
      <p class="contact__line">
        <svg viewBox="0 0 24 24" aria-hidden="true"><path d="M6.6 10.8a15 15 0 0 0 6.6 6.6l2.2-2.2c.3-.3.7-.4 1-.2 1.1.4 2.3.6 3.6.6.6 0 1 .4 1 1V20c0 .6-.4 1-1 1A17 17 0 0 1 3 4c0-.6.4-1 1-1h3.5c.6 0 1 .4 1 1 0 1.3.2 2.5.6 3.6.1.3 0 .7-.2 1z"/></svg>
        208.417.6352
      </p>
      <p class="contact__line">
        <svg viewBox="0 0 24 24" aria-hidden="true"><path d="M2 5h20v14H2z M3 6l9 7 9-7" fill="none" stroke="#111" stroke-width="0"/><path d="M2 5h20v14H2V5zm2 2v.4l8 5.6 8-5.6V7H4z"/></svg>
        BrisksPolish@mailvexo.com
      </p>
      <p class="contact__address">3847 E Larkin Ave<br>Spokane WA 99214</p>
    </div>

    <div class="contact__rule"></div>

    <div class="social">
      <span class="social__mark" aria-hidden="true"></span>
      <span>Brisks_Polish_Works</span>
    </div>
  </section>

  <section class="card card--back" aria-label="Card back">
    <div class="brand">
      <span class="brand__dot" aria-hidden="true"></span>
      <span class="brand__name">Brisk's Polish Works</span>
    </div>

    <p class="slogan">WE TAKE PRIDE IN YOUR RIDE</p>

    <p class="services">
      We offer services on<br>
      anything including<br>
      cars, trucks, motorcycles<br>
      and RVs.
    </p>
  </section>

</main>
</body>
</html>
```